Vantro cards

I am in the auto motive, transportation business I would like a business card that is Something cool, modern edgy, having to do with car culture. I offer towing service for high and exotic cars. I also provide towing for collisions and car accidents. I offer open and enclosed transport nationwide.

Target Market(s)

Car culture people high end auto collectors

Industry/Entity Type

Towing car carrier

Contact Information for Business Card

My company colors black yellow and silver

Font styles to use
Serif

```html
<!DOCTYPE html>
<html lang="en">
<head>
<meta charset="utf-8">
<title>Vantro Transportation — Business Card</title>
<link href="https://fonts.googleapis.com/css2?family=Montserrat:wght@400;600;800&display=swap" rel="stylesheet">
<style>
  :root {
    --backdrop: #e4e1dc;
    --card: #ffffff;
    --ink: #111111;
    --text: #2b2b2b;
    --navy: #1d2340;
    --yellow: #f7dc57;
    --muted: #d8d8d8;
  }
  * { margin: 0; padding: 0; box-sizing: border-box; }
  html, body { width: 900px; height: 1200px; overflow: hidden; }
  body {
    position: relative;
    background: var(--backdrop);
    font-family: "Montserrat", Arial, sans-serif;
    color: var(--text);
  }
  .card {
    position: absolute;
    left: 80px;
    width: 742px;
    height: 443px;
    background: var(--card);
    border-radius: 28px;
    overflow: hidden;
    box-shadow: 0 8px 18px rgba(0,0,0,0.28);
  }
  .card--front { top: 132px; }
  .card--back { top: 638px; }

  .brand {
    position: absolute;
    display: flex;
    align-items: center;
    gap: 12px;
  }
  .brand__mark { width: 26px; height: 26px; background: var(--yellow); flex: none; }
  .brand__name {
    font-weight: 800;
    color: var(--ink);
    text-transform: uppercase;
    line-height: 1.05;
  }
  .card--front .brand { left: 36px; top: 105px; }
  .card--front .brand__name { font-size: 26px; }
  .card--back .brand { left: 0; right: 0; top: 170px; justify-content: center; }
  .card--back .brand__mark { width: 36px; height: 36px; }
  .card--back .brand__name { font-size: 38px; }

  .holder { position: absolute; left: 35px; top: 256px; }
  .holder__name { font-size: 26px; font-weight: 600; color: var(--yellow); line-height: 1.2; }
  .holder__role { font-size: 16px; color: var(--navy); margin-top: 2px; }

  .divider {
    position: absolute; left: 33px; top: 314px;
    width: 676px; height: 2px; background: var(--ink);
  }

  .contacts { position: absolute; left: 35px; top: 326px; list-style: none; }
  .contacts li {
    display: flex; align-items: center; gap: 10px;
    font-size: 16px; height: 21px; color: var(--text);
  }
  .contacts svg { width: 14px; height: 14px; fill: var(--ink); flex: none; }

  .address {
    position: absolute; left: 530px; top: 348px;
    font-size: 16px; line-height: 21px; color: var(--text);
    font-style: normal;
  }

  .front-band { position: absolute; left: 0; bottom: 0; width: 742px; height: 45px; }

  .back-stripe {
    position: absolute; left: 0; top: 364px;
    width: 742px; height: 6px; background: var(--yellow);
  }
  .back-band {
    position: absolute; left: 0; top: 382px;
    width: 742px; height: 61px; background: var(--ink);
    display: flex; align-items: center; justify-content: center;
    color: var(--muted); font-size: 16px; letter-spacing: 0.2px;
  }
</style>
</head>
<body>

  <section class="card card--front" aria-label="Card front">
    <div class="brand">
      <span class="brand__mark"></span>
      <span class="brand__name">Vantro<br>Transportation</span>
    </div>

    <div class="holder">
      <p class="holder__name">Daniel Reyes</p>
      <p class="holder__role">Owner</p>
    </div>

    <div class="divider"></div>

    <ul class="contacts">
      <li>
        <svg viewBox="0 0 16 16" aria-hidden="true"><path d="M2 5c0-2 2-3 6-3s6 1 6 3v1h-3V5H5v1H2z M4 7h8l2 6H2z"/></svg>
        (555) 014-2280
      </li>
      <li>
        <svg viewBox="0 0 16 16" aria-hidden="true"><path d="M1 3h14v10H1z M1 3l7 6 7-6" stroke="#fff" stroke-width="1.2"/></svg>
        info@vantrotransportation.com
      </li>
      <li>
        <svg viewBox="0 0 16 16" aria-hidden="true"><circle cx="8" cy="8" r="7"/></svg>
        www.vantrotransportation.com
      </li>
    </ul>

    <address class="address">48 Harbor Street<br>Millbrook, PA 17000</address>

    <svg class="front-band" viewBox="0 0 742 45" preserveAspectRatio="none" aria-hidden="true">
      <rect x="0" y="10" width="440" height="7" fill="var(--yellow)"/>
      <path d="M0 20 L430 20 C448 20 448 0 470 0 L742 0 L742 45 L0 45 Z" fill="var(--ink)"/>
    </svg>
  </section>

  <section class="card card--back" aria-label="Card back">
    <div class="brand">
      <span class="brand__mark"></span>
      <span class="brand__name">Vantro Transportation</span>
    </div>
    <div class="back-stripe"></div>
    <div class="back-band">www.vantrotransportation</div>
  </section>

</body>
</html>
```